The Aldermoor- outdoor banner

This should be a horizontal banner. It should have the logos attached incorporated and the following details
Coming Spring 2025: The Aldermoor - Exclusive Luxury Condos
Listed by Marisol Quennell | Fairlight Realty
Construction by Stonegate Build Group
Unveil the height of luxury living with The Aldermoor, a new condo building in East Boston, set for completion in Spring 2025. Experience a standard of elegance and sophistication like never before.
For more information and inquiries, please contact:
Marisol Quennell
Phone: (617) 430-9162
Email: marisol@fairlightprops.com
The banner should be very classy incorporting gold and navy very classic fonts. The Aldermoor should look very classy and exclusive. The stonegate build group logo should be smaller. It should not include their phone number and instagram handle only the name of the company. Herringbone pattern in the background would be great. This is going outside the building to advertise pre construction units

```html
<!DOCTYPE html>
<html lang="en">
<head>
<meta charset="utf-8">
<title>The Aldermoor — Exclusive Luxury Condos</title>
<link rel="stylesheet" href="https://fonts.googleapis.com/css2?family=Cinzel:wght@400;500&family=Didact+Gothic&family=Montserrat:wght@700&display=swap">
<style>
  :root {
    --navy-deep: #18213f;
    --navy: #26325a;
    --navy-soft: #3a4a78;
    --ink: #2a3452;
    --white: #ffffff;
    --silver-light: #f1f1f1;
    --silver: #b9b9b9;
    --rule: #c9c9c9;
  }
  * { box-sizing: border-box; margin: 0; padding: 0; }
  html, body { width: 1200px; height: 600px; overflow: hidden; background: var(--white); }
  .banner { position: relative; width: 1200px; height: 600px; overflow: hidden; background: var(--white); }

  .hero {
    position: absolute; left: 0; top: 0; width: 1200px; height: 422px;
    background:
      radial-gradient(ellipse 520px 300px at 330px 110px, rgba(70,88,140,.55), transparent 70%),
      linear-gradient(90deg, var(--navy) 0%, var(--navy-deep) 60%, #141b36 100%);
  }
  .silver-band {
    position: absolute; left: 0; top: 422px; width: 1200px; height: 10px;
    background: linear-gradient(90deg, var(--silver) 0%, var(--silver-light) 50%, var(--silver) 100%);
  }

  .serif { font-family: "Cinzel", "Times New Roman", serif; color: var(--white); text-shadow: 2px 3px 5px rgba(0,0,0,.55); }
  .launch { position: absolute; left: 0; width: 822px; text-align: center; top: 76px; font-size: 51px; letter-spacing: 1px; }
  .the { position: absolute; left: 368px; width: 92px; text-align: center; top: 172px; font-size: 33px; font-weight: 500; }
  .rule { position: absolute; height: 1.5px; background: var(--white); box-shadow: 0 2px 3px rgba(0,0,0,.4); }
  .rule-top-left { left: 178px; top: 200px; width: 190px; }
  .rule-top-right { left: 460px; top: 200px; width: 188px; }
  .rule-bottom { left: 108px; top: 297px; width: 642px; }
  .name { position: absolute; left: 102px; width: 650px; top: 186px; text-align: center; font-weight: 400; line-height: 1; white-space: nowrap; }
  .name .cap { font-size: 118px; }
  .name .mid { font-size: 88px; letter-spacing: 1px; }
  .tagline { position: absolute; left: 0; width: 850px; top: 316px; text-align: center; font-size: 41px; }

  .pitch { position: absolute; left: 803px; width: 360px; text-align: center; color: var(--white); text-transform: uppercase; }
  .pitch-lead { top: 97px; font-family: "Didact Gothic", "Century Gothic", sans-serif; font-size: 21.5px; line-height: 25px; }
  .pitch-strong { top: 266px; font-family: "Montserrat", "Century Gothic", sans-serif; font-weight: 700; font-size: 19px; line-height: 25px; }

  .label { font-family: "Montserrat", "Century Gothic", sans-serif; font-weight: 700; color: var(--ink); text-transform: uppercase; text-align: center; position: absolute; }
  .listed-by { left: 32px; width: 160px; top: 476px; font-size: 16px; }
  .agent-stack { left: 32px; width 160px; width: 160px; top: 505px; font-size: 24px; line-height: 25px; }

  .brokerage-mark { position: absolute; left: 274px; top: 451px; width: 76px; height: 76px; border: 3px solid var(--ink); border-radius: 50%; }
  .brokerage-name { position: absolute; left: 200px; width: 224px; top: 532px; text-align: center; font-family: "Cinzel", "Times New Roman", serif; color: var(--ink); line-height: 1; }
  .brokerage-name .main { display: block; font-size: 25px; font-weight: 500; }
  .brokerage-name .sub { display: block; font-size: 13px; font-weight: 500; letter-spacing: 5px; margin-top: 5px; }

  .divider { position: absolute; top: 455px; width: 2px; height: 118px; background: linear-gradient(180deg, transparent, var(--rule) 20%, var(--rule) 80%, transparent); }
  .divider-one { left: 446px; }
  .divider-two { left: 655px; }

  .construction-by { left: 459px; width: 182px; top: 463px; font-size: 16px; }
  .builder-name { left: 459px; width: 182px; top: 532px; font-size: 13px; letter-spacing: .5px; }

  .contact-intro { left: 680px; width: 496px; top: 467px; font-size: 14.5px; }
  .contact-name { left: 680px; width: 496px; top: 496px; font-size: 33px; letter-spacing: 1px; }
  .contact-line { position: absolute; left: 680px; width: 496px; top: 537px; display: flex; justify-content: center; align-items: center; gap: 4px; font-family: "Montserrat", "Century Gothic", sans-serif; font-weight: 700; font-size: 19px; color: var(--ink); }
  .contact-line .item { display: inline-flex; align-items: center; gap: 4px; margin-right: 4px; }
  .contact-line svg { width: 22px; height: 22px; flex: none; }
</style>
</head>
<body>
<main class="banner">
  <div class="hero" role="img" aria-label="Softly lit photo of a luxury condo living and dining room in deep navy tones"></div>
  <div class="silver-band"></div>

  <p class="launch serif">Coming Spring 2025</p>
  <span class="rule rule-top-left"></span>
  <p class="the serif">The</p>
  <span class="rule rule-top-right"></span>
  <h1 class="name serif"><span class="cap">A</span><span class="mid">LDERMOO</span><span class="cap">R</span></h1>
  <span class="rule rule-bottom"></span>
  <p class="tagline serif">Exclusive Luxury Condos</p>

  <p class="pitch pitch-lead">Unveil the height of<br>luxury living with the<br>Aldermoor, a new<br>condo building in<br>East Boston, set for<br>completion in Spring 2025.</p>
  <p class="pitch pitch-strong">Experience a standard<br>of elegance and<br>sophistication like<br>never before.</p>

  <p class="label listed-by">Listed by</p>
  <p class="label agent-stack">Marisol<br>Quennell</p>

  <span class="brokerage-mark"></span>
  <p class="brokerage-name"><span class="main">FAIRLIGHT</span><span class="sub">REALTY</span></p>

  <span class="divider divider-one"></span>

  <p class="label construction-by">Construction by</p>
  <p class="label builder-name">Stonegate Build Group</p>

  <span class="divider divider-two"></span>

  <p class="label contact-intro">For more information and inquiries, please contact</p>
  <p class="label contact-name">Marisol Quennell</p>
  <p class="contact-line">
    <span class="item">
      <svg viewBox="0 0 24 24" aria-hidden="true"><circle cx="12" cy="12" r="12" fill="#2a3452"/><path d="M8.2 6.5c.5-.4 1.1-.3 1.4.2l1.1 1.8c.3.5.2 1-.2 1.4l-.7.6c.6 1.4 1.6 2.5 3 3.1l.6-.7c.4-.4 1-.5 1.4-.2l1.8 1.1c.5.3.6.9.2 1.4l-.8 1c-.6.7-1.6.9-2.5.5-3-1.3-5.2-3.6-6.4-6.5-.3-.9-.1-1.9.6-2.4z" fill="#fff"/></svg>
      (617) 430-9162
    </span>
    <span class="item">
      <svg viewBox="0 0 24 24" aria-hidden="true"><circle cx="12" cy="12" r="12" fill="#2a3452"/><rect x="6.5" y="8" width="11" height="8" rx="1" fill="none" stroke="#fff" stroke-width="1.5"/><path d="M6.8 8.5 12 12.5l5.2-4" fill="none" stroke="#fff" stroke-width="1.5"/></svg>
      marisol@fairlightprops.com
    </span>
  </p>
</main>
</body>
</html>
```